9x12 Business Brochure, 3 fold, for Internet Marketing Company

I'd like to have a brochure designed for my Internet marketing company. I have the content all ready, 10 Internet Marketing Myths, which you can see here: http://www.brisklanternstudio.example/usual-web-promotion-fables/. I'm looking for something creative and business to business. The company is all about Internet marketing. I like the "http://" header I use at our website. People like it too and identify with it. Audience is business owners 35 to 55 years old. I use blue at my website. I *think* I would like the cover page (front page) to open with some attention grabbing text, that basically takes most of the front page of the brochure. It would probably say: "I Can Help You Get BETTER RESULTS from Your Website, More Traffic, TOP RANKINGS at Quorble, More Leads and MORE SALES. But first you'll have to avoid these common Internet marketing myths..." The inside pages would have the content from above (the 10 myths). The back page would have testimonials that I can provide. And the inside folded in page (or what I call the inside folded in page) would have a list of services. I think I want the dimensions 12x9 which is a larger sized, three-fold brochure.

Target Market(s)

I use this brochure to send to business owners and managers to show them I know what I'm talking about and and expert. See attachment for content.

Industry/Entity Type

Marketing

Requirements
Should not have
• No clipart. Probably not illustrations. Photos. The "http://" used at the site is something people "connect" with and get that this is about Internet marketing.

```html
<!DOCTYPE html>
<html lang="en">
<head>
<meta charset="utf-8">
<title>Common Internet Marketing Myths – Brochure Inside</title>
<link rel="stylesheet" href="https://fonts.googleapis.com/css2?family=Open+Sans:wght@400;600&family=Roboto+Condensed:wght@700&family=Arimo:wght@700&display=swap">
<style>
:root{
  --blue-left:#4a86bf;
  --blue-right:#4c8ac3;
  --blue-band:#3f7cb6;
  --blue-heading:#3d86c8;
  --rule:#2f6aa3;
  --dark-bar:#2d2d2d;
  --ink:#2f2f2f;
  --white:#ffffff;
  --pale:#f3f5f7;
}
*{margin:0;padding:0;box-sizing:border-box}
html,body{width:1200px;height:924px;overflow:hidden;background:#fff}
.brochure{position:relative;width:1200px;height:924px;font-family:"Open Sans",Arial,sans-serif}
.panel{position:absolute;top:0;height:924px;width:400px}
.panel--front{left:0;background:linear-gradient(180deg,var(--blue-left),#3e78b0 60%,var(--blue-left));color:var(--white)}
.panel--back{left:400px;background:linear-gradient(90deg,#d9dde2 0%,var(--pale) 35%,#fff 55%,#e4e7eb 100%);color:var(--ink)}
.panel--right{left:800px;background:linear-gradient(160deg,#5a97cc,var(--blue-right) 40%,#3f7bb3);color:var(--white)}
.top-band{position:absolute;top:0;left:0;width:1200px;height:30px;background:var(--blue-band)}
.top-band::after{content:"";position:absolute;left:400px;top:0;width:400px;height:30px;background:linear-gradient(90deg,#cfd4da,#fff 50%,#e2e5e9)}
.title-bar{position:absolute;top:30px;left:0;height:66px;width:1000px;background:linear-gradient(180deg,#4a4a4a,var(--dark-bar));clip-path:polygon(0 0,955px 0,1000px 66px,0 66px)}
.title-bar h1{font-family:"Roboto Condensed",Arial,sans-serif;font-weight:700;font-size:29px;color:#fff;line-height:66px;padding-left:48px;letter-spacing:.3px}
.address-photo{position:absolute;top:30px;left:860px;width:340px;height:72px;background:linear-gradient(180deg,#e8eef5,#9fb8d2 60%,#5a86b6);clip-path:polygon(0 0,340px 0,340px 72px,50px 72px)}
.myth{position:absolute;left:30px;width:340px}
.myth__label{display:flex;align-items:center;font-size:14px;line-height:18px}
.myth__label::after{content:"";flex:1;height:1px;background:var(--rule);margin-left:4px;margin-top:4px}
.panel--back .myth__label::after{background:#9aa3ad}
.myth__title{font-weight:600;font-size:18px;line-height:21px;margin:3px 0 12px}
.panel--back .myth__title{color:var(--blue-heading)}
.myth__body{font-size:11.4px;line-height:16.6px;text-align:justify}
.tagline{position:absolute;left:0;top:793px;width:400px;height:38px;background:var(--dark-bar);color:#fff;font-family:"Roboto Condensed",Arial,sans-serif;font-weight:700;font-size:21px;line-height:38px;text-align:center}
.call{position:absolute;top:840px;left:0;width:400px;text-align:center;font-family:Arimo,Arial,sans-serif;font-size:19px;font-weight:700;color:#333}
.call em{font-style:italic;font-weight:400;font-size:15px}
.company{position:absolute;top:872px;left:0;width:400px;text-align:center;font-family:Arimo,Arial,sans-serif;font-weight:700;font-size:17px;color:var(--blue-heading)}
.site{position:absolute;top:873px;left:0;width:400px;text-align:center;font-family:Arimo,Arial,sans-serif;font-weight:700;font-size:15px;color:#1d1d1d}
</style>
</head>
<body>
<main class="brochure">
  <section class="panel panel--front">
    <article class="myth" style="top:129px">
      <p class="myth__label">Myth #1</p>
      <h2 class="myth__title">If you build it they will come</h2>
      <p class="myth__body">Building a website is no guarantee of online success. If you build it, don’t assume people will find it. This is a guaranteed losing strategy. For your Internet marketing to succeed your website will need quality traffic (i.e. visitor sessions) and then convert those visitors into phone calls and online inquiries.</p>
    </article>
    <article class="myth" style="top:311px">
      <p class="myth__label">Myth #2</p>
      <h2 class="myth__title">Search engines are all you’ll need</h2>
      <p class="myth__body">It is a very common misconception, and costly mistake, to think that search engines and organic search engine positioning is all you need for online success. While a top ranked website is a very valuable asset, and it can drive a lot of qualified traffic to your website, it can take months, or years, to achieve that positioning — if you can get it at all. You’ll need a multi-pronged approach to building traffic, including buying advertising, pay-per-click advertising (PPC), integration of your offline marketing with your online marketing, blogging, social media, and of course, search engine optimization (SEO).</p>
    </article>
    <article class="myth" style="top:573px">
      <p class="myth__label">Myth #3</p>
      <h2 class="myth__title">All traffic is good</h2>
      <p class="myth__body">Not true! To get real results from your website, inquiries, phone calls, and sales, you’ll need to find and attract QUALIFIED traffic – people who are actually getting married and who are ready to purchase your products and services.</p>
    </article>
    <article class="myth" style="top:737px">
      <p class="myth__label">Myth #4</p>
      <h2 class="myth__title">Hits are a good measure of success</h2>
      <p class="myth__body">Wrong! If you are measuring “hits” you’re not even in the game. A “hit” is a technical term that describes activity on a hosting server. Unfortunately, most webmasters use this term casually and it is interpreted to mean you have lots of traffic. Hits are not real people. Real people who visit your website are logged as “visitor sessions.”</p>
    </article>
  </section>

  <section class="panel panel--back">
    <article class="myth" style="top:129px">
      <p class="myth__label">Myth #5</p>
      <h2 class="myth__title">You can do this all yourself</h2>
      <p class="myth__body">If you are in any competitive category of products or services, or in a geographically competitive marketplace, the chances that you can build a website, develop the traffic, and manage your ongoing online marketing ALL BY YOURSELF are less than one in ten. Put another way, DIY has a 90% chance of FAILURE.</p>
    </article>
    <article class="myth" style="top:313px">
      <p class="myth__label">Myth #6</p>
      <h2 class="myth__title">It’s easy to get traffic from search engines</h2>
      <p class="myth__body">In today’s competitive marketplace it is more difficult than ever to get top ranking with Quorble, Zentrix!, or Plumo. It is very likely going to take six to twelve months to see your website achieve a top ranked position for any competitive keyword/keyword phrase that people are searching for – and that’s only if you have SEO expertise. If your website is new it will take longer.</p>
    </article>
    <article class="myth" style="top:540px">
      <p class="myth__label">Myth #7</p>
      <h2 class="myth__title">Submitting your website to search engines actually works</h2>
      <p class="myth__body">Not true! Submitting your website to the search engines each month is USELESS. Companies or individuals that provide this service will gladly take your money and it is unlikely you’ll see any benefit. The best way to get your website indexed in the search engines is for them to find your website link at another regularly crawled, thematically-similar website. A Quorble Sitemap will also help you get your website indexed and crawled more effectively.</p>
    </article>
    <p class="tagline">More Traffic. More Inquiries. More Sales.</p>
    <p class="call"><em>Call - </em>(555) 014-2387</p>
    <p class="company">Brisk Lantern Studio (.example)</p>
  </section>

  <section class="panel panel--right">
    <article class="myth" style="top:129px">
      <p class="myth__label">Myth #8</p>
      <h2 class="myth__title">Search engine optimization is easy</h2>
      <p class="myth__body">Search engine optimization is not difficult but there is a lot to it. There are dozens of different variables that must be perfectly managed. Each of these falls into one of two categories: “on-page” variables or “off-page” variables. Add to this hundreds of so-called “experts” and their advice (which is incorrect, incomplete, or misleading), and it’s pretty hard to call the search engine optimization process easy. Getting top ranked is even more challenging when a competitor has hired a reputable SEO expert to help them with their website and Internet marketing strategy.</p>
    </article>
    <article class="myth" style="top:394px">
      <p class="myth__label">Myth #9</p>
      <h2 class="myth__title">Meta-Tags are the key to a top ranked website</h2>
      <p class="myth__body">Meta-tags are specific lines of programming code that appear behind-the-scenes at your website. Search engines see them but your visitors do not. Search engines use meta-tags as one of the factors in determining page relevancy. Quorble’s algorithm tries to show the most relevant pages for a search on a search engine results page (SERP). Meta-tags are still important, but only one of more than two dozen factors related to the overall search engine optimization of your website.</p>
    </article>
    <article class="myth" style="top:652px">
      <p class="myth__label">Myth #10</p>
      <h2 class="myth__title">Your Webmaster / Programmer Can Help You With Your Internet Marketing</h2>
      <p class="myth__body">Graphics design, programming code, and page layout are very different from Internet marketing. In most cases, (90% of the time) a webmaster / programmer will not be able to give you the appropriate advice or support to effectively promote and market your website online.</p>
    </article>
    <p class="site">http://www.brisklanternstudio.example</p>
  </section>

  <div class="top-band"></div>
  <header class="title-bar"><h1>Common Internet Marketing Myths</h1></header>
  <div class="address-photo" role="img" aria-label="Photo of a browser address bar showing http://www close-up"></div>
</main>
</body>
</html>
```